Website Design for a different kind of Business Consulting organisation needed!

We need a website design that reflects who we are, the simplicity of our consulting business and with a focus on our priority - to help our clients deliver, or execute - the "e" in Vantor-i.

Our key high level requirements are:
1) Simple and intuitive look and feel
2) Integration with all key social media platforms, twitter, facebook, linkedin, tumblr.

10 pages, tops.
- Main page - Welcome
- About Us/ Who are Vantor-i?
- 5 services pages - Project Management, Business Process Management, Change Management, Business Analysis and Finance Systems
- Contact Us

Something like:
http://www.lumvexhold.example/

Vantor-i is a registered trademark and all Logos and other branded material are attached for reference.

So, what’s our gig: A few snippets from previous work...

We are a different kind of business consulting group. We partner with our clients to help them deliver change. We don't just provide them with the theory. We also provide them with the leadership and capability to execute the change.

We aren’t a one stop shop, and we don’t offer cookie cutter solutions. We’re a boutique consulting firm covering Project Management, Business Process Management, Change Management and Business Analytics.

Vantor-i is a professional services organisation that partners with their clients to lead the execution of strategic process and system improvement initiatives. Vantor-i combines hands on delivery with coaching in best practice methodologies and approaches to build their clients capabilities to ensure their ongoing success in project implementations.

UPDATES:

Thanks to everyone who has submitted designs so far. The standard of designs coming through is quite high, with lots of professional designs that nail the design brief. Eliminating them is proving to be quite challenging.

A few updates to the job brief:
- Please make sure the design fits on one page. We would like all of our information to be on the first page that people see without them having to scroll down
- Please ensure you include the FIVE services we offer in the design
- Please use corporate images/istock photos in your designs which are relevant to our business
- Please add a section for a live twitter feed from our twitter account and a link to google+
- Please add a section for news/updates

Also, if you are able to build a site once a design is selected, please let us know.

Thanks,

Maribel.

Target Market(s)

Our target customers are large enterprises in Australia that are growing rapidly and have recently (last 24 months) undertaken or are currently undergoing software implementations and business process improvement programs. These businesses have a turnover of $100m or above and are working hard to differentiate themselves from their competitors but are not seeing the return on investment promised by software vendors and process improvement initiatives.

Industry/Entity Type

Leadership

Requirements
Must have
• Collaboration / Training / Workshop / Consulting images all of a professional nature.
Simple, non-cluttered look with plenty of white space.

```html
<!DOCTYPE html>
<html lang="en">
<head>
<meta charset="utf-8">
<title>Vantor-i | Contact Us</title>
<link rel="stylesheet" href="https://fonts.googleapis.com/css2?family=Open+Sans:wght@400;600;700&display=swap">
<style>
:root{
  --brand:#0157a6;
  --ink:#444444;
  --heading:#4a4a4a;
  --muted:#8c8c8c;
  --field-bg:#f9f9f9;
  --field-line:#bdbdbd;
  --rule:#e4e4e4;
  --map-base:#e8e4dc;
  --white:#ffffff;
}
*{box-sizing:border-box;margin:0;padding:0}
html,body{width:1200px;height:1120px;overflow:hidden;background:var(--white)}
body{position:relative;font-family:"Open Sans",Arial,sans-serif;color:var(--ink)}
.abs{position:absolute}
.top-band{left:0;top:0;width:1200px;height:7px;background:var(--brand)}
.brand{left:118px;top:22px;font-size:58px;font-weight:400;color:var(--brand);line-height:1;letter-spacing:1px}
.social-top{left:922px;top:17px;display:flex;gap:9px}
.social-top span{width:32px;height:32px;border-radius:50%;background:#8a8a8a}
.social-top span.active{background:var(--brand)}
.main-nav{left:504px;top:71px;display:flex;font-size:16px;font-weight:600;color:var(--muted)}
.main-nav a{color:inherit;text-decoration:none;height:24px;line-height:24px;padding:0 10px;margin-right:26px}
.main-nav a:last-child{margin-right:0;margin-left:8px}
.main-nav a.current{background:var(--brand);color:var(--white)}
.header-rule{left:120px;top:113px;width:958px;height:2px;background:var(--rule)}
.page-title{left:119px;top:141px;font-size:30px;font-weight:700;color:var(--brand)}
.intro{left:119px;top:179px;width:965px;font-size:16px;line-height:25px}
.section-title{font-size:20px;font-weight:600;color:var(--heading)}
.label{font-size:16px;color:var(--ink)}
.field{background:var(--field-bg);border:1px solid var(--field-line);font-size:16px;color:#b8b8b8;padding:5px 14px;line-height:21px}
.field.focus{border:2px solid var(--brand);padding:4px 13px}
.field.small{font-size:14px;padding:6px 7px}
.captcha{background:#dcdcdc}
.submit{left:120px;top:815px;width:119px;height:39px;background:var(--brand);color:var(--white);font-size:16px;text-align:center;line-height:39px}
.map{left:691px;top:342px;width:386px;height:360px;background:linear-gradient(160deg,#ebe7df,#e3ded4);border:1px solid #cfcfcf}
.address{left:691px;top:708px;font-size:16px;line-height:25px}
.contact-row{display:flex;align-items:center;font-size:16px}
.contact-row svg{margin-right:9px}
.footer{left:0;top:998px;width:1200px;height:122px;background:var(--brand);color:var(--white)}
.footer h4{font-size:14px;font-weight:700;position:absolute}
.footer p,.footer a{font-size:13px;color:var(--white);text-decoration:none;line-height:19px}
.foot-social{left:120px;top:65px;display:flex;gap:9px}
.foot-social span{width:32px;height:32px;border-radius:50%;background:var(--white)}
.foot-brand{left:865px;top:16px;font-size:44px;font-weight:400;line-height:1}
</style>
</head>
<body>
<div class="abs top-band"></div>
<div class="abs brand">Vantor-i</div>
<div class="abs social-top"><span></span><span class="active"></span><span></span><span></span></div>
<nav class="abs main-nav"><a>HOME</a><a>ABOUT</a><a>SERVICES</a><a>PARTNERS</a><a class="current">CONTACT</a></nav>
<div class="abs header-rule"></div>

<h1 class="abs page-title">Contact Us</h1>
<p class="abs intro">Sed ut perspiciatis unde omnis iste natus error sit voluptatem accusantium doloremque laudantium, totam rem aperiam, eaque ipsa quae ab illo inventore veritatis et quasi architecto beatae vitae dicta sunt explicabo.</p>

<h2 class="abs section-title" style="left:120px;top:286px">Contact Form</h2>
<div class="abs label" style="left:122px;top:320px">Name:</div>
<div class="abs field" style="left:121px;top:345px;width:505px;height:33px">Enter you name</div>
<div class="abs label" style="left:122px;top:392px">Email Address:</div>
<div class="abs field focus" style="left:120px;top:416px;width:506px;height:35px">Enter your email</div>
<div class="abs label" style="left:122px;top:467px">Subject:</div>
<div class="abs field" style="left:121px;top:492px;width:505px;height:33px">Enter subject</div>
<div class="abs label" style="left:122px;top:541px">Message:</div>
<div class="abs field" style="left:121px;top:566px;width:504px;height:139px">Enter Message</div>
<div class="abs label" style="left:122px;top:718px">Type code shown</div>
<div class="abs label" style="left:274px;top:718px">Code:</div>
<svg class="abs" style="left:318px;top:720px" width="20" height="20" viewBox="0 0 20 20"><rect x="0.5" y="0.5" width="19" height="19" fill="#fff" stroke="#777"/><path d="M5 10a5 5 0 0 1 9-3M15 10a5 5 0 0 1-9 3" fill="none" stroke="#555" stroke-width="1.5"/><path d="M14 4v3h-3M6 16v-3h3" fill="none" stroke="#555" stroke-width="1.5"/></svg>
<div class="abs field small" style="left:121px;top:743px;width:137px;height:33px">Type Code here</div>
<div class="abs field" style="left:274px;top:743px;width:123px;height:33px;padding:0;background:#fff">
  <div class="abs captcha" role="img" aria-label="Verification code image" style="left:16px;top:6px;width:90px;height:20px"></div>
</div>
<div class="abs submit">Submit</div>

<h2 class="abs section-title" style="left:694px;top:284px">Location Map</h2>
<div class="abs map" role="img" aria-label="Street map showing the office location"></div>
<p class="abs address">Level 10, 72 Harbour St. Melbourne<br>Australia, 3000</p>

<h2 class="abs section-title" style="left:690px;top:793px">Contact Details</h2>
<div class="abs contact-row" style="left:690px;top:830px">
  <svg width="22" height="22" viewBox="0 0 22 22"><circle cx="11" cy="11" r="11" fill="var(--brand)"/><path d="M6 8c0-2 10-2 10 0v1h-3v-1h-4v1H6z M7 10h8l1 6H6z" fill="#fff"/></svg>+61 3 555 014 218</div>
<div class="abs contact-row" style="left:690px;top:860px">
  <svg width="22" height="22" viewBox="0 0 22 22"><circle cx="11" cy="11" r="11" fill="var(--brand)"/><rect x="8" y="5" width="6" height="4" fill="#fff"/><rect x="5" y="9" width="12" height="6" rx="1" fill="#fff"/><rect x="8" y="13" width="6" height="4" fill="#fff" stroke="var(--brand)"/></svg>+61 3 5550 1987</div>
<div class="abs contact-row" style="left:894px;top:830px">
  <svg width="22" height="22" viewBox="0 0 22 22"><circle cx="11" cy="11" r="11" fill="var(--brand)"/></svg>@vantor-i</div>
<div class="abs contact-row" style="left:894px;top:860px">
  <svg width="22" height="22" viewBox="0 0 22 22"><circle cx="11" cy="11" r="11" fill="var(--brand)"/><rect x="5" y="7" width="12" height="8" fill="#fff"/><path d="M5 7l6 5 6-5" fill="none" stroke="var(--brand)" stroke-width="1.3"/></svg>info@vantor-i.example</div>

<footer class="abs footer">
  <h4 style="left:120px;top:21px">CONNECT WITH US</h4>
  <p class="abs" style="left:120px;top:40px">on social media network</p>
  <div class="abs foot-social"><span></span><span></span><span></span><span></span></div>
  <h4 style="left:330px;top:21px">PAGES</h4>
  <div class="abs" style="left:330px;top:40px;display:flex;flex-direction:column"><a>Home</a><a>About</a><a>Services</a></div>
  <div class="abs" style="left:405px;top:40px;display:flex;flex-direction:column"><a>Term &amp; Conditions</a><a>FAQ</a><a>Partners</a></div>
  <h4 style="left:567px;top:21px">CONTACT DETAILS</h4>
  <p class="abs" style="left:567px;top:40px">p: +61 3 555 014 218&nbsp; f: +61 3 5550 1987<br>Level 10, 72 Harbour St. Melbourne,<br>Australia, 3000</p>
  <div class="abs foot-brand">Vantor-i</div>
  <p class="abs" style="left:866px;top:74px">Copyright © 2014 All Rights Reserved</p>
</footer>
</body>
</html>
```